Awesome photographers card for an awesome new business

Double sided business card Black background and silver logo in middle on one side. Details on otherside. please keep it simple

Industry/Entity Type

Photographer

Contact Information for Business Card

Gerald Fenwick
0452817360
GeraldFenwickPhotography47@mailbox.test
www.GeraldFenwickPhotography.test.au
Instagram _Gerald_fenwick

Requirements
Must have
• My logo in Silver
• please use instagram logo instead of "Instagram"

```html
<!DOCTYPE html>
<html lang="en">
<head>
<meta charset="utf-8">
<title>Gerald Fenwick Photography – Business Card</title>
<link rel="stylesheet" href="https://fonts.googleapis.com/css2?family=Open+Sans:wght@400;600;700&display=swap">
<style>
  :root {
    --backdrop: #3a3a3a;
    --card: #0c0c0d;
    --card-edge: #1a1a1c;
    --silver: #d9d9d9;
    --silver-soft: #bdbdbd;
    --divider: #3c3c3e;
    --text: #e6e6e6;
  }
  * { box-sizing: border-box; margin: 0; padding: 0; }
  html, body {
    width: 1200px; height: 900px; overflow: hidden;
    background: var(--backdrop);
    font-family: "Open Sans", Arial, sans-serif;
  }
  .stage {
    width: 1200px; height: 900px;
    display: flex; align-items: center; justify-content: center; gap: 60px;
  }
  .card {
    width: 525px; height: 300px;
    background: var(--card);
    border: 1px solid var(--card-edge);
    border-radius: 22px;
    position: relative;
    box-shadow: 0 10px 30px rgba(0,0,0,.45);
  }
  .brand-mark {
    display: flex; align-items: center; gap: 12px;
    color: var(--silver);
    font-weight: 600;
    font-size: 17px;
    letter-spacing: .04em;
    white-space: nowrap;
  }
  .brand-mark .dot {
    width: 14px; height: 14px; border-radius: 50%;
    background: var(--silver);
    flex: none;
  }
  /* details side */
  .card--details { display: flex; }
  .card--details .logo-zone {
    width: 205px;
    display: flex; align-items: center; justify-content: center;
    border-right: 1px solid var(--divider);
    margin: 40px 0;
  }
  .card--details .brand-mark { font-size: 14px; gap: 8px; }
  .card--details .brand-mark .dot { width: 11px; height: 11px; }
  .contact {
    flex: 1;
    padding: 72px 0 0 24px;
    color: var(--text);
  }
  .contact .name {
    font-size: 17px; font-weight: 700; margin-bottom: 14px; color: var(--silver);
  }
  .contact ul { list-style: none; }
  .contact li {
    display: flex; align-items: center; gap: 10px;
    font-size: 12.5px; line-height: 22px; white-space: nowrap;
  }
  .contact svg { width: 12px; height: 12px; flex: none; fill: var(--silver-soft); }
  .social-square {
    width: 11px; height: 11px; flex: none;
    background: var(--silver-soft); border-radius: 2px;
  }
  /* logo side */
  .card--logo {
    display: flex; align-items: center; justify-content: center;
  }
</style>
</head>
<body>
<main class="stage">
  <section class="card card--details" aria-label="Business card, contact side">
    <div class="logo-zone">
      <div class="brand-mark"><span class="dot"></span>Gerald Fenwick</div>
    </div>
    <div class="contact">
      <p class="name">Gerald Fenwick</p>
      <ul>
        <li>
          <svg viewBox="0 0 24 24" aria-hidden="true"><path d="M6.6 10.8a15.1 15.1 0 0 0 6.6 6.6l2.2-2.2a1 1 0 0 1 1-.25 11.4 11.4 0 0 0 3.6.57 1 1 0 0 1 1 1V20a1 1 0 0 1-1 1A17 17 0 0 1 3 4a1 1 0 0 1 1-1h3.5a1 1 0 0 1 1 1c0 1.25.2 2.45.57 3.57a1 1 0 0 1-.25 1z"/></svg>
          0452817360
        </li>
        <li>
          <svg viewBox="0 0 24 24" aria-hidden="true"><path d="M2 5h20v14H2zm2 2v.5l8 5 8-5V7zm0 2.9V17h16V9.9l-8 5z"/></svg>
          GeraldFenwickPhotography47@mailbox.test
        </li>
        <li>
          <svg viewBox="0 0 24 24" aria-hidden="true"><path d="M12 2a10 10 0 1 0 0 20 10 10 0 0 0 0-20zm6.9 6h-3a15.7 15.7 0 0 0-1.3-3.9A8 8 0 0 1 18.9 8zM12 4c.8 1.2 1.5 2.5 1.9 4h-3.8c.4-1.5 1.1-2.8 1.9-4zM4.3 14a8 8 0 0 1 0-4h3.4a16 16 0 0 0 0 4zm.8 2h3a15.7 15.7 0 0 0 1.3 3.9A8 8 0 0 1 5.1 16zm3-8h-3a8 8 0 0 1 4.3-3.9A15.7 15.7 0 0 0 8.1 8zM12 20c-.8-1.2-1.5-2.5-1.9-4h3.8c-.4 1.5-1.1 2.8-1.9 4zm2.3-6H9.7a14 14 0 0 1 0-4h4.6a14 14 0 0 1 0 4zm.3 5.9a15.7 15.7 0 0 0 1.3-3.9h3a8 8 0 0 1-4.3 3.9zm1.7-5.9a16 16 0 0 0 0-4h3.4a8 8 0 0 1 0 4z"/></svg>
          www.GeraldFenwickPhotography.test.au
        </li>
        <li>
          <span class="social-square" aria-hidden="true"></span>
          _Gerald_fenwick
        </li>
      </ul>
    </div>
  </section>

  <section class="card card--logo" aria-label="Business card, logo side">
    <div class="brand-mark"><span class="dot"></span>Gerald Fenwick</div>
  </section>
</main>
</body>
</html>
```